Kesso Tea Premium Matcha brand Label

This is a label design project for a luxury tea brand. Feel free to be creative within the guidelines.
Attached to this project is a document called “Private Label Design Requirements” with the design guidelines and template. There is another document called "Kesso Tea Packaging Instructions" this has more details necessary to stick to the guidelines in the first document.

I have also attached the certifications to be included as well as different variations of the logo for you to use.

If you have any questions, I am here.
Updates

Need extra days to review

Target Market(s)

Young, active, fun, enjoy the finer things

```html
<!DOCTYPE html>
<html lang="en">
<head>
<meta charset="utf-8">
<title>Kesso Tea – Premium Organic Ceremonial Matcha Label</title>
<link rel="stylesheet" href="https://fonts.googleapis.com/css2?family=Open+Sans:wght@400;600&display=swap">
<style>
  :root {
    --canvas: #7b7b7d;
    --trim: #e05a5a;
    --dieline: #2e2e30;
    --safe-line: #3aa3dc;
    --panel-left: #5b5552;
    --panel-mid: #a3a3a4;
    --panel-right: #6d6d6f;
    --photo-tone: #6a5a50;
    --text: #ffffff;
    --text-soft: #ececec;
    --accent: #2aa0d8;
    --seal-fill: #f4f4f0;
    --seal-ring: #6b4a2e;
    --mark: #ffffff;
  }
  * { margin: 0; padding: 0; box-sizing: border-box; }
  html, body { width: 1200px; height: 234px; overflow: hidden; }
  body { font-family: "Open Sans", sans-serif; color: var(--text); background: var(--canvas); }

  .label-sheet {
    position: relative; width: 1200px; height: 234px;
    background: var(--canvas); border: 1px solid var(--trim);
  }
  .dieline {
    position: absolute; left: 20px; top: 20px; width: 1160px; height: 193px;
    border: 1px solid var(--dieline); border-radius: 22px;
  }
  .safe-area {
    position: absolute; left: 64px; top: 39px; width: 1072px; height: 155px;
    border: 1px dashed var(--safe-line); border-radius: 16px; overflow: hidden;
    background: linear-gradient(90deg, var(--panel-left) 0%, #6e6966 30%, var(--panel-mid) 52%, #8a8a8b 70%, var(--panel-right) 100%);
  }
  .teaware-photo {
    position: absolute; left: 0; top: 0; width: 440px; height: 100%;
    background: radial-gradient(ellipse at 62% 55%, rgba(140,95,70,.55) 0%, rgba(106,90,80,.35) 45%, rgba(90,85,82,0) 80%);
  }
  .leaf-photo {
    position: absolute; right: 0; top: 0; width: 280px; height: 100%;
    background: radial-gradient(ellipse at 75% 50%, rgba(150,140,110,.35) 0%, rgba(110,110,112,0) 75%);
  }

  .distributor {
    position: absolute; left: 74px; top: 89px;
    font-size: 15.5px; line-height: 20.5px; font-weight: 400;
  }

  .brand {
    position: absolute; left: 445px; top: 40px; width: 300px; text-align: center;
  }
  .brand-dot {
    display: block; width: 44px; height: 44px; margin: 4px auto 0;
    border-radius: 50%; background: var(--mark); opacity: .9;
  }
  .brand-name { font-size: 25px; line-height: 30px; font-weight: 400; margin-top: 6px; }
  .brand-product { font-size: 13.5px; line-height: 18px; font-weight: 600; margin-top: 9px; }
  .brand-weight { font-size: 20px; line-height: 24px; font-weight: 400; margin-top: 0; }

  .ingredients {
    position: absolute; left: 815px; top: 43px;
  }
  .ingredients-title { font-size: 13.5px; line-height: 18px; font-weight: 600; }
  .ingredients-list { font-size: 14px; line-height: 20px; font-weight: 600; margin-top: 2px; }
  .ingredients-rule { width: 85px; height: 2px; background: var(--accent); margin: 5px 0 4px; }
  .prep-steps { list-style: none; font-size: 11.3px; line-height: 14.6px; color: var(--text-soft); }
  .prep-steps li::before { content: "• "; }

  .organic-seal {
    position: absolute; left: 947px; top: 146px; width: 40px; height: 40px;
    border-radius: 50%; background: var(--seal-fill); border: 2px solid var(--seal-ring);
  }
  .storage-note {
    position: absolute; left: 1000px; top: 148px;
    font-size: 13.5px; line-height: 17.5px; font-weight: 400; color: var(--text-soft);
    text-transform: uppercase; letter-spacing: .2px;
  }
</style>
</head>
<body>
<main class="label-sheet">
  <div class="dieline"></div>
  <section class="safe-area">
    <div class="teaware-photo" role="img" aria-label="Photo of a clay teapot, tea bowls and matcha powder on a wooden table"></div>
    <div class="leaf-photo" role="img" aria-label="Faded photo of green tea leaves and a cup of tea"></div>
  </section>

  <div class="distributor">
    <p>Distributed by Kesso Tea Co. | Riverside, Ga</p>
    <p>Certified Organic by Verdane</p>
    <p>PRODUCT OF JAPAN</p>
  </div>

  <div class="brand">
    <span class="brand-dot"></span>
    <h1 class="brand-name">Kesso Tea</h1>
    <p class="brand-product">Premium Organic Ceremonial Matcha</p>
    <p class="brand-weight">Net Wt: 30g</p>
  </div>

  <div class="ingredients">
    <h2 class="ingredients-title">Ingredients</h2>
    <p class="ingredients-list">Premium Organic Japanese Matcha Green Tea</p>
    <div class="ingredients-rule"></div>
    <ul class="prep-steps">
      <li>2 tsp of Matcha</li>
      <li>2oz of Water (170-180 degrees F)</li>
      <li>Whisk in a W formation until frothy</li>
      <li>Sweeten to taste</li>
    </ul>
  </div>

  <div class="organic-seal" role="img" aria-label="Organic certification seal"></div>
  <p class="storage-note">Keep refrigerated<br>for quality</p>
</main>
</body>
</html>
```